Packaging card Design

we are going to offer a general assortment of action cam mounts. currently all action/sports cam vendors offer their assortment of mounts, we want to offer 1 assortment suitable for all major brands.
here we will request 1 topcard for the (bag) package, but the total job will be designing 7 to 15 ones (same bbasics, small changes)
please google "zentiq headstrap mount packaging" and you find an image of the original Zentiq packaging (carton top with plastic bag). we need the design of the topcard.
description:
FRONT:
- create VEX-grip logo (to be placed on top of card)
- product name (in this example the Head Strap)
- suitable for:
* Zentiq
* UBT Lumivex / Ventaqo
* Bolna HD
* Veltrim
* oKEL / uZA / RASO
* Tavek / QMR
* Sable Orchard Nuo
BACK:
in centre a drawing of the item with a camera (Zentiq Falk7) mounted on it. only the line drawing of the headstrap must be bold and the cam light..
around it we mention all the brands mentioned on the front and mention it is compatible in 4 languages (English / French / Dutch / German.
so what we get is:
Zentiq:
Compatible
Kompatibel
(for other accesories we might state here that a 'tripod mount' is needed to fit)
+ we mention the URL www.VEX-grips.eu
color scheme can be either Zentiq style (black + logo blue/white) or you can create your own mixture (please do not forget the BLACK & blue & white of Zentiq is recognisable).
Reason: we started the project late due to Briefnest authorisation and many of you just recently accepted the offer, next to that we made it a guaranteed project yesterday so this prolongation gives you more time to submit.
kind regards,
Tobias
Zentiq clients (sportive, but more over getting a mainstreme product)
Plastic

```html
<!DOCTYPE html>
<html lang="en">
<head>
<meta charset="utf-8">
<title>VEX-grip Head Strap – Top Card</title>
<link rel="stylesheet" href="https://fonts.googleapis.com/css2?family=Quicksand:wght@300;400;700&display=swap">
<style>
  :root {
    --backdrop: #e6e6e6;
    --card: #ffffff;
    --ink: #111111;
    --hang-hole: #b1b1b1;
    --brand-blue: #2350a0;
    --card-shadow: rgba(0, 0, 0, 0.35);
  }
  * { box-sizing: border-box; margin: 0; padding: 0; }
  html, body {
    width: 1200px;
    height: 561px;
    overflow: hidden;
    background: var(--backdrop);
    font-family: "Quicksand", sans-serif;
    color: var(--ink);
  }
  .top-card {
    position: absolute;
    left: 28px;
    top: 13px;
    width: 1144px;
    height: 534px;
    background: var(--card);
    box-shadow: 0 1px 4px var(--card-shadow);
  }
  .hang-hole {
    position: absolute;
    left: 455px;
    top: 66px;
    width: 234px;
    height: 84px;
  }
  .brand-lockup {
    position: absolute;
    right: 52px;
    top: 168px;
    display: flex;
    align-items: center;
    gap: 16px;
  }
  .brand-name {
    font-weight: 700;
    font-size: 62px;
    line-height: 1;
    letter-spacing: 1px;
    color: var(--ink);
  }
  .brand-mark {
    width: 34px;
    height: 34px;
    background: var(--brand-blue);
  }
  .product-name {
    position: absolute;
    left: 70px;
    top: 376px;
    font-weight: 300;
    font-size: 68px;
    line-height: 1;
    letter-spacing: 0.5px;
  }
  .product-tagline {
    position: absolute;
    left: 71px;
    top: 468px;
    font-weight: 400;
    font-size: 20px;
    line-height: 1;
  }
  .guarantee-seal {
    position: absolute;
    left: 962px;
    top: 362px;
    width: 126px;
    height: 126px;
  }
</style>
</head>
<body>
  <main class="top-card">
    <svg class="hang-hole" viewBox="0 0 234 84" aria-hidden="true">
      <circle cx="117" cy="27" r="24" fill="var(--hang-hole)"/>
      <rect x="0" y="38" width="234" height="40" rx="20" fill="var(--hang-hole)"/>
    </svg>

    <div class="brand-lockup">
      <span class="brand-name">VEX-grip</span>
      <span class="brand-mark" aria-hidden="true"></span>
    </div>

    <h1 class="product-name">Head Strap</h1>
    <p class="product-tagline">Compatible with all major action cameras</p>

    <svg class="guarantee-seal" viewBox="0 0 126 126" aria-hidden="true">
      <circle cx="63" cy="63" r="60" fill="none" stroke="var(--ink)" stroke-width="2.5"/>
    </svg>
  </main>
</body>
</html>
```